Unique Business Card Design

Unique Business Card design for our orthotic and prosthetic company. Our logo is on our website, color is light blue. Unique shape (artificial leg shaped, vertical, etc..) preferred. Logo, business name, individual name and basic demographics needed.

Industry/Entity Type

Business

Contact Information for Business Card

Logo, Industry, Phone # Logo, "Prosthetic & Orthotic Services" Place to add individual name and contact info

Colors
cee9f5

Requirements
Must have
• The icon must be there, placement of "Prosthetic & Orthotic Services" can be moved
Nice to have
• Like the mix of light blue, and a little darker blue. One design included the icons from my website which was a nice touch

```html
<!DOCTYPE html>
<html lang="en">
<head>
<meta charset="utf-8">
<title>Stridewell Inc. — Business Cards</title>
<link rel="stylesheet" href="https://fonts.googleapis.com/css2?family=Open+Sans:wght@400;600;700&family=Lora:ital@1&display=swap">
<style>
  :root {
    --brand-blue: #1a5aa8;
    --brand-blue-deep: #15509a;
    --card-white: #ffffff;
    --backdrop: #e8ebee;
    --ink-on-blue: #ffffff;
  }
  * { box-sizing: border-box; margin: 0; padding: 0; }
  html, body { width: 1200px; height: 812px; overflow: hidden; }
  body {
    background: var(--backdrop);
    font-family: "Open Sans", Arial, sans-serif;
    position: relative;
  }
  .card {
    position: absolute;
    width: 520px;
    height: 297px;
    background: var(--card-white);
    overflow: hidden;
    box-shadow: 0 2px 6px rgba(0,0,0,.08);
  }
  .card--front { left: 45px; top: 258px; }
  .card--back  { left: 635px; top: 258px; }

  /* Front */
  .front-lockup {
    position: absolute;
    left: 58px; top: 104px;
    display: flex; align-items: center; gap: 22px;
  }
  .brand-dot {
    width: 92px; height: 92px; border-radius: 50%;
    background: var(--brand-blue);
    flex: none;
  }
  .brand-name {
    color: var(--brand-blue);
    font-weight: 600;
    font-size: 31px;
    letter-spacing: .5px;
    line-height: 1;
    white-space: nowrap;
  }
  .brand-rule {
    height: 2px; background: var(--brand-blue);
    margin: 6px 0 4px;
  }
  .brand-tagline {
    font-family: "Lora", Georgia, serif;
    font-style: italic;
    color: var(--brand-blue);
    font-size: 15px;
    text-align: right;
    white-space: nowrap;
  }

  /* Back */
  .back-panel {
    position: absolute; inset: 0;
    background: var(--brand-blue-deep);
    clip-path: polygon(44% 0, 100% 0, 100% 100%, 54% 100%, 52% 62%, 44% 34%);
  }
  .figure-area {
    position: absolute;
    left: 205px; top: 70px;
    width: 130px; height: 227px;
    background: linear-gradient(180deg, var(--brand-blue-deep), var(--brand-blue));
    clip-path: polygon(30% 0, 60% 0, 70% 30%, 100% 55%, 85% 100%, 35% 100%, 20% 65%, 0 40%, 15% 15%);
  }
  .back-brand {
    position: absolute;
    left: 22px; top: 148px;
    transform: translateY(-50%) rotate(-90deg) translateX(0);
    transform-origin: center;
  }
  .back-brand-wrap {
    position: absolute;
    left: -60px; top: 120px;
    width: 260px;
    transform: rotate(-90deg);
  }
  .back-brand-wrap .brand-name { font-size: 27px; }
  .back-brand-wrap .brand-tagline { font-size: 13px; }

  .contact {
    position: absolute;
    right: 26px; top: 26px;
    color: var(--ink-on-blue);
    text-align: right;
  }
  .contact-name { font-size: 19px; font-weight: 400; line-height: 1.1; }
  .contact-name strong { font-weight: 700; }
  .contact-title { font-size: 12px; letter-spacing: 1px; margin-bottom: 4px; }
  .contact-email { font-size: 11px; margin-bottom: 22px; }
  .contact-phones { list-style: none; font-size: 12.5px; line-height: 1.55; margin-bottom: 22px; }
  .contact-phones li { display: flex; justify-content: flex-end; align-items: center; gap: 7px; }
  .contact-phones svg { width: 11px; height: 12px; fill: none; stroke: var(--ink-on-blue); stroke-width: 1.6; }
  .contact-address { font-style: normal; font-size: 12.5px; line-height: 1.5; }
</style>
</head>
<body>

<section class="card card--front" aria-label="Card front">
  <div class="front-lockup">
    <span class="brand-dot" aria-hidden="true"></span>
    <div class="brand-block">
      <div class="brand-name">STRIDEWELL INC.</div>
      <div class="brand-rule"></div>
      <div class="brand-tagline">Prosthetic &amp; Orthotic Services</div>
    </div>
  </div>
</section>

<section class="card card--back" aria-label="Card back">
  <div class="back-panel"></div>
  <div class="figure-area" role="img" aria-label="Blue silhouette of a walking person with a prosthetic leg"></div>

  <div class="back-brand-wrap">
    <div class="brand-name">STRIDEWELL INC.</div>
    <div class="brand-rule"></div>
    <div class="brand-tagline">Prosthetic &amp; Orthotic Services</div>
  </div>

  <div class="contact">
    <div class="contact-name"><strong>Miriam</strong> Castell</div>
    <div class="contact-title">CO LPO</div>
    <div class="contact-email">mcastell@stridewellinc.com</div>
    <ul class="contact-phones">
      <li>555.214.3300
        <svg viewBox="0 0 12 12" aria-label="Office phone"><path d="M2 1.5h2.5l1 2.5-1.5 1a6 6 0 0 0 3 3l1-1.5 2.5 1V10a1.5 1.5 0 0 1-1.5 1.5A9 9 0 0 1 .5 3 1.5 1.5 0 0 1 2 1.5z"/></svg>
      </li>
      <li>555.214.3301
        <svg viewBox="0 0 12 12" aria-label="Fax"><rect x="1" y="4" width="10" height="6" rx="1"/><path d="M3 4V1h6v3"/></svg>
      </li>
      <li>555-387-2046
        <svg viewBox="0 0 12 12" aria-label="Mobile"><rect x="3" y="1" width="6" height="10" rx="1"/></svg>
      </li>
    </ul>
    <address class="contact-address">
      820 Harbor Lane<br>
      Fairview, NY 10000<br>
      www.stridewellinc.com
    </address>
  </div>
</section>

</body>
</html>
```